Coastline Premier Retreats Business Card Design

Design a business card for Coastline Premier Retreats. Look at the website for colors and reference. Card should have logo, name, title, office number, mobile number, email, URL and a tagline like, "Luxury Hotel & Resort Email Marketing" (This might change).

https://www.coastlinepremierretreats.example

The rest I will leave up to your imagination.

Contact Information for Business Card

Logo, name, title, office number, mobile number, email, URL and a tagline like, "Luxury Hotel & Resort Email Marketing" (This might change).

```html
<!DOCTYPE html>
<html lang="en">
<head>
<meta charset="utf-8">
<title>Coastline Premier Retreats – Business Card</title>
<link rel="stylesheet" href="https://fonts.googleapis.com/css2?family=Open+Sans:wght@400;600;700&display=swap">
<style>
  :root {
    --backdrop: #232323;
    --card: #fffff4;
    --orange: #f07022;
    --ink: #141414;
  }
  * { box-sizing: border-box; margin: 0; padding: 0; }
  html, body {
    width: 1200px; height: 780px; overflow: hidden;
    background: var(--backdrop);
    font-family: "Open Sans", Arial, sans-serif;
  }
  .canvas { position: relative; width: 1200px; height: 780px; }
  .card {
    position: absolute;
    width: 520px; height: 297px;
    background: var(--card);
    border-radius: 22px;
    overflow: hidden;
    box-shadow: 0 14px 34px rgba(0,0,0,.55);
  }
  .card--front { left: 70px; top: 80px; }
  .card--back  { left: 610px; top: 400px; }

  .brand-name {
    font-weight: 700;
    color: var(--ink);
    text-transform: uppercase;
    line-height: 1.05;
    display: flex; align-items: center; gap: 12px;
  }
  .brand-mark { width: 14px; height: 14px; background: var(--orange); flex: none; }
  .card--front .brand-name {
    position: absolute; left: 0; right: 0; top: 50%;
    transform: translateY(-50%);
    justify-content: center;
    font-size: 30px; letter-spacing: 1px;
  }
  .card--back .brand-name {
    position: absolute; left: 30px; top: 34px;
    font-size: 17px; letter-spacing: .5px; gap: 8px;
  }
  .card--back .brand-mark { width: 10px; height: 10px; }

  .holder {
    position: absolute; right: 44px; top: 96px; text-align: right;
  }
  .holder-name { font-size: 25px; font-weight: 700; line-height: 1.1; }
  .holder-first { color: var(--orange); }
  .holder-last { color: var(--ink); }
  .holder-title { font-size: 13px; color: var(--ink); margin-top: 2px; }
  .accent-tab {
    position: absolute; right: 0; top: 92px;
    width: 20px; height: 50px; background: var(--orange);
  }

  .tagline {
    position: absolute; left: 30px; top: 150px;
    font-size: 13px; line-height: 1.4; color: var(--orange);
  }
  .contact-list {
    position: absolute; left: 30px; bottom: 22px;
    list-style: none;
    font-size: 12.5px; color: var(--ink); line-height: 1.55;
  }
  .contact-list li { display: flex; align-items: center; gap: 8px; }
  .contact-icon { width: 12px; height: 12px; flex: none; }
</style>
</head>
<body>
<main class="canvas">

  <section class="card card--front" aria-label="Business card front">
    <div class="brand-name"><span class="brand-mark"></span>Coastline Premier Retreats</div>
  </section>

  <section class="card card--back" aria-label="Business card back">
    <div class="brand-name"><span class="brand-mark"></span>Coastline Premier Retreats</div>

    <div class="accent-tab"></div>
    <div class="holder">
      <p class="holder-name"><span class="holder-first">Marta</span> <span class="holder-last">Velinska</span></p>
      <p class="holder-title">Managing Director</p>
    </div>

    <p class="tagline">Luxury Hotel &amp;<br>Resort Email Marketing</p>

    <ul class="contact-list">
      <li>
        <svg class="contact-icon" viewBox="0 0 24 24" aria-hidden="true"><path fill="#f07022" d="M6.6 10.8a15.1 15.1 0 0 0 6.6 6.6l2.2-2.2c.3-.3.7-.4 1-.2 1.1.4 2.3.6 3.6.6.6 0 1 .4 1 1V20c0 .6-.4 1-1 1A17 17 0 0 1 3 4c0-.6.4-1 1-1h3.5c.6 0 1 .4 1 1 0 1.3.2 2.5.6 3.6.1.3 0 .7-.2 1z"/></svg>
        (555) 010-2758
      </li>
      <li>
        <svg class="contact-icon" viewBox="0 0 24 24" aria-hidden="true"><rect x="6" y="2" width="12" height="20" rx="2" fill="none" stroke="#f07022" stroke-width="2"/><circle cx="12" cy="18" r="1.2" fill="#f07022"/></svg>
        (555) 010-7777
      </li>
      <li>
        <svg class="contact-icon" viewBox="0 0 24 24" aria-hidden="true"><circle cx="12" cy="12" r="10" fill="none" stroke="#f07022" stroke-width="2"/><path d="M2 12h20M12 2c3 3 3 17 0 20M12 2c-3 3-3 17 0 20" fill="none" stroke="#f07022" stroke-width="1.6"/></svg>
        www.coastlinepremierretreats.example
      </li>
      <li>
        <svg class="contact-icon" viewBox="0 0 24 24" aria-hidden="true"><rect x="2" y="5" width="20" height="14" rx="1.5" fill="#f07022"/><path d="M3 6l9 7 9-7" fill="none" stroke="#fffff4" stroke-width="1.6"/></svg>
        info@coastlinepremierretreats.example
      </li>
    </ul>
  </section>

</main>
</body>
</html>
```